New Business Card Design Project

I'd like a business card design around the same modern style that I used on my website www.brovanhs.com
It's gonna be one of those round corners double-sided business cards with maybe a big logo on the front and all the info on the back of the card.

Contact Information for Business Card

Marco Delgado
425-317-6084
www.brovanhs.com

www.facebook.com/BrovanHomeServices
www.intsgram.com/BrovanHomeServices

Requirements
Must have
• it needs to look elegant and modern

```html
<!DOCTYPE html>
<html lang="en">
<head>
<meta charset="utf-8">
<title>Brovan Home Services – Business Cards</title>
<link rel="stylesheet" href="https://fonts.googleapis.com/css2?family=Open+Sans:wght@400;600;700;800&display=swap">
<style>
  :root {
    --page-bg: #e9e7e3;
    --card-white: #f4f4f4;
    --brand-blue: #1bb0dc;
    --brand-blue-deep: #0a8fc0;
    --ink-dark: #231f20;
    --text-light: #ffffff;
    --text-ink: #2b2b2b;
  }
  * { margin: 0; padding: 0; box-sizing: border-box; }
  html, body {
    width: 1200px; height: 780px; overflow: hidden;
    background: var(--page-bg);
    font-family: "Open Sans", Arial, sans-serif;
  }
  .canvas {
    position: relative; width: 1200px; height: 780px;
    display: flex; align-items: center; justify-content: center; gap: 40px;
  }
  .card {
    position: relative; width: 540px; height: 309px;
    border-radius: 22px; overflow: hidden;
    background: var(--card-white);
    box-shadow: 0 10px 24px rgba(0,0,0,.18);
  }
  .card-shapes { position: absolute; inset: 0; width: 100%; height: 100%; }
  .brand-name {
    position: absolute;
    color: var(--brand-blue);
    font-weight: 800;
    letter-spacing: -0.5px;
    line-height: 1.05;
  }
  /* Back card */
  .card-back .brand-name { left: 40px; top: 58px; font-size: 40px; width: 300px; }
  .contact-name {
    position: absolute; left: 150px; top: 214px;
    color: var(--text-light); font-weight: 700; font-size: 19px;
  }
  .contact-divider {
    position: absolute; left: 298px; top: 198px; width: 1.5px; height: 56px;
    background: var(--text-light); opacity: .85;
  }
  .contact-lines {
    position: absolute; left: 314px; top: 200px;
    color: var(--text-light); font-size: 13px; line-height: 26px;
  }
  .contact-line { display: flex; align-items: center; gap: 8px; }
  .contact-line svg { width: 13px; height: 13px; }
  .social-line {
    position: absolute; left: 0; right: 0; bottom: 0; height: 40px;
    display: flex; align-items: center; justify-content: center;
    font-size: 14px; color: var(--text-light);
  }
  .social-line .social-label { color: var(--brand-blue); margin-right: 6px; }
  /* Front card */
  .card-front .brand-name { left: 180px; top: 86px; font-size: 46px; width: 330px; }
  .front-web {
    position: absolute; left: 36px; top: 268px;
    color: var(--text-light); font-size: 15px; letter-spacing: 3px;
  }
</style>
</head>
<body>
<main class="canvas">

  <section class="card card-back" aria-label="Business card, contact side">
    <svg class="card-shapes" viewBox="0 0 540 309" preserveAspectRatio="none" aria-hidden="true">
      <defs>
        <linearGradient id="blueBandBack" x1="0" y1="0" x2="1" y2="1">
          <stop offset="0" stop-color="#1fb8e3"/>
          <stop offset="1" stop-color="#0a8fc0"/>
        </linearGradient>
      </defs>
      <path d="M0,196 C220,186 400,116 456,0" fill="none" stroke="#231f20" stroke-width="7"/>
      <path d="M0,205 C225,196 410,124 468,0 L540,0 L540,309 L0,309 Z" fill="url(#blueBandBack)"/>
      <rect x="0" y="269" width="540" height="40" fill="#231f20"/>
    </svg>

    <div class="brand-name">Brovan Home Services</div>

    <div class="contact-name">Marco Delgado</div>
    <div class="contact-divider"></div>
    <div class="contact-lines">
      <div class="contact-line">
        <svg viewBox="0 0 14 14" aria-hidden="true"><rect x="3" y="1" width="8" height="12" rx="1.5" fill="none" stroke="#fff" stroke-width="1.4"/><circle cx="7" cy="11" r=".9" fill="#fff"/></svg>
        <span>425-317-6084</span>
      </div>
      <div class="contact-line">
        <svg viewBox="0 0 14 14" aria-hidden="true"><circle cx="7" cy="7" r="6" fill="#fff"/><path d="M1,7 H13 M7,1 C4,4 4,10 7,13 M7,1 C10,4 10,10 7,13" fill="none" stroke="#0a8fc0" stroke-width=".9"/></svg>
        <span>www.brovanhs.com</span>
      </div>
    </div>

    <div class="social-line"><span class="social-label">facebook/intsgram:</span><span>BrovanHomeServices</span></div>
  </section>

  <section class="card card-front" aria-label="Business card, logo side">
    <svg class="card-shapes" viewBox="0 0 540 309" preserveAspectRatio="none" aria-hidden="true">
      <defs>
        <linearGradient id="blueBandFront" x1="0" y1="0" x2="1" y2="1">
          <stop offset="0" stop-color="#1fb8e3"/>
          <stop offset="1" stop-color="#0a8fc0"/>
        </linearGradient>
      </defs>
      <path d="M0,130 C150,220 330,258 540,258" fill="none" stroke="#231f20" stroke-width="7"/>
      <path d="M0,142 C150,230 330,266 540,266 L540,309 L0,309 Z" fill="url(#blueBandFront)"/>
    </svg>

    <div class="brand-name">Brovan Home Services</div>
    <div class="front-web">www.brovanhs.com</div>
  </section>

</main>
</body>
</html>
```